Seed Oil Safety Card for Healthy Restaurant Dining

I am seeking a design for a physical card to communicate my wife's health-related dietary restriction regarding seed oils. This card will be given to restaurant waiters to ensure her meals are prepared without seed oils, as it is a health issue and not merely a preference.
My wife cannot eat any “seed oil” or “processed oil”, including:
- Vegetable oil
- Canola oil
- Soybean oil
- Sunflower oil
- Corn oil
- Cottonseed oil
- Safflower oil
- Peanut oil
- Sesame oil
Oils that are OK for her to consume:
- Butter (most preferable)
- Extra virgin olive oil
- Avocado oil
- Coconut oil
- Ghee
- Lard
- Any other animal-based fats
Key Design Requirements:
- Clarity and speed of communication: The card should be easily read and understood by waiters, even in low-light environments, emphasizing that it's a health concern.
- Avoid common misconceptions: Ensure the design doesn't imply common dietary preferences like "vegetarian" or "no butter." Animal fats and butter are actually preferable for her!
- Preferred term: Use "seed oils" as the term to describe what she cannot eat due to her health issue.
- Trace amounts are acceptable: Communicate that it's OK to use cookware that has previously been in contact with seed oils, but not to have seed oil as an ingredient. Please suggest a concise way to convey this.
- Card dimensions: Design should be 3.5” x 2.25” (standard credit-card size on printorvale.example). Horizontal or vertical layouts are both fine, whichever makes the message clearer.
Design Suggestions:
- Utilize bold and easy-to-read typography to communicate the main message.
- Consider incorporating relevant icons or graphics that help convey the message without adding confusion.
- Use contrasting colors to enhance readability, especially in low-light situations.
- To communicate the “trace amounts OK” part, consider phrases such as:
- "Cross-contamination acceptable"
- “Used cookware OK, no ingredient use”
- “Separate cookware not necessary”
Thank you for your assistance in creating this essential card for my wife's health and safety when dining out!

```html
<!DOCTYPE html>
<html lang="en">
<head>
<meta charset="utf-8">
<title>Seed Oil Dietary Restriction Card</title>
<link href="https://fonts.googleapis.com/css2?family=Lato:ital,wght@0,400;0,700;0,900;1,400&display=swap" rel="stylesheet">
<style>
  :root {
    --backdrop: #dfe0e2;
    --brand-blue: #1b6db3;
    --alert-red: #c8202f;
    --safe-green: #6a9e2f;
    --ink: #1f1f1f;
    --list-ink: #333333;
    --card-white: #ffffff;
    --mist: #e4e7ec;
  }
  * { margin: 0; padding: 0; box-sizing: border-box; }
  html, body {
    width: 1200px; height: 2743px; overflow: hidden;
    background: var(--backdrop);
    font-family: "Lato", Arial, sans-serif;
  }
  .card {
    position: absolute; left: 150px; top: 671px;
    width: 900px; height: 1401px;
    background: linear-gradient(170deg, var(--card-white) 55%, var(--mist) 100%);
    border-radius: 48px; overflow: hidden;
    box-shadow: 0 18px 30px rgba(0,0,0,0.28);
  }
  .card-header {
    position: absolute; left: 0; top: 0; width: 100%; height: 192px;
    background: var(--brand-blue); color: #fff; text-align: center;
  }
  .card-header .kicker {
    position: absolute; top: 36px; left: 11px; width: 100%;
    font-size: 50px; font-weight: 400; letter-spacing: 22px; line-height: 1;
  }
  .card-header .title {
    position: absolute; top: 98px; width: 100%;
    font-size: 65px; font-weight: 900; line-height: 1;
  }
  .status-icon { position: absolute; width: 76px; height: 76px; }
  .section-heading {
    position: absolute; left: 139px;
    font-size: 41px; font-weight: 900; line-height: 44px; color: var(--ink);
    white-space: nowrap;
  }
  .section-heading .warn { color: var(--alert-red); }
  .section-heading .ok { color: var(--safe-green); }
  .oil-list { position: absolute; list-style: none; }
  .oil-list li {
    position: relative; padding-left: 40px;
    font-size: 50px; line-height: 56px; color: var(--list-ink); white-space: nowrap;
  }
  .oil-list li::before {
    content: ""; position: absolute; left: 2px; top: 24px;
    width: 13px; height: 13px; border-radius: 50%; background: var(--list-ink);
  }
  .list-divider {
    position: absolute; left: 439px; top: 373px; width: 8px; height: 259px;
    background: var(--alert-red);
  }
  .trace-note {
    position: absolute; left: 66px; top: 659px;
    font-size: 44px; font-style: italic; line-height: 44px; color: var(--ink);
    white-space: nowrap;
  }
  .trace-note span { display: block; padding-left: 16px; }
  .medical-mark {
    position: absolute; left: 545px; top: 820px; width: 355px; height: 400px;
    background: radial-gradient(circle at 50% 50%, rgba(190,198,210,0.45), rgba(220,224,230,0) 70%);
  }
  .card-footer {
    position: absolute; left: 0; bottom: 0; width: 100%; height: 78px;
    background: var(--brand-blue); color: #fff; text-align: center;
    font-size: 33px; font-weight: 700; letter-spacing: 5px; line-height: 78px;
  }
</style>
</head>
<body>
  <div class="card">
    <header class="card-header">
      <div class="kicker">HEALTH-RELATED</div>
      <div class="title">DIETARY RESTRICTION</div>
    </header>

    <svg class="status-icon" style="left:40px; top:237px;" viewBox="0 0 76 76" aria-hidden="true">
      <circle cx="38" cy="38" r="37" fill="#c8202f"/>
      <path d="M24 24 L52 52 M52 24 L24 52" stroke="#fff" stroke-width="10" stroke-linecap="round"/>
    </svg>
    <h2 class="section-heading" style="top:217px;">PLEASE MAKE SURE THAT MY<br>MEALS ARE PREPARED WITHOUT<br>ANY <span class="warn">SEED OILS/PROCESSED OILS</span>:</h2>

    <ul class="oil-list" style="left:66px; top:365px;">
      <li>Vegetable oil</li>
      <li>Canola oil</li>
      <li>Soybean oil</li>
      <li>Sunflower oil</li>
      <li>Corn oil</li>
    </ul>
    <div class="list-divider"></div>
    <ul class="oil-list" style="left:478px; top:365px;">
      <li>Cottonseed oil</li>
      <li>Safflower oil</li>
      <li>Peanut oil</li>
      <li>Sesame oil</li>
    </ul>

    <p class="trace-note">*Trace amounts are acceptable<span>Separate cookwares are not necessary</span></p>

    <div class="medical-mark" role="img" aria-label="Faint medical emblem watermark"></div>

    <svg class="status-icon" style="left:40px; top:803px;" viewBox="0 0 76 76" aria-hidden="true">
      <circle cx="38" cy="38" r="37" fill="#6a9e2f"/>
      <path d="M21 39 L33 51 L56 26" stroke="#fff" stroke-width="9" fill="none" stroke-linecap="round" stroke-linejoin="round"/>
    </svg>
    <h2 class="section-heading" style="top:793px;"><span class="ok">OTHER OILS</span> THAT ARE SAFE<br>TO USE:</h2>

    <ul class="oil-list" style="left:66px; top:902px;">
      <li>Butter (most preferable)</li>
      <li>Extra virgin olive oil</li>
      <li>Avocado oil</li>
      <li>Coconut oil</li>
      <li>Ghee</li>
      <li>Lard</li>
      <li>Any other animal-based fats</li>
    </ul>

    <footer class="card-footer">THANK YOU FOR KEEPING ME SAFE</footer>
  </div>
</body>
</html>
```